Estate Planning Law Firm opening new branch in Florida

I am an experienced estate planning attorney that recently relocated to Florida. Looking for a banner Ad to place on platforms such as HomeLane, Chatterbox and Picturely to create publicity for firm and new leads.

```html
<!DOCTYPE html>
<html lang="en">
<head>
<meta charset="UTF-8">
<title>Serenova Law Firm – Estate &amp; Financial Planning Banner</title>
<link href="https://fonts.googleapis.com/css2?family=Montserrat:wght@600;700&display=swap" rel="stylesheet">
<style>
  :root {
    --navy-deep: #16263a;
    --navy: #1f3550;
    --slate: #3b5572;
    --warm: #e89a4a;
    --teal: #2fa99b;
    --white: #ffffff;
    --soft-white: #e9eef3;
  }
  html, body {
    margin: 0;
    padding: 0;
    width: 1200px;
    height: 444px;
    overflow: hidden;
    background: var(--navy-deep);
  }
  .banner {
    position: relative;
    width: 1200px;
    height: 444px;
    overflow: hidden;
    font-family: "Montserrat", Arial, sans-serif;
    color: var(--white);
  }
  .banner__photo {
    position: absolute;
    inset: 0;
    background:
      radial-gradient(circle at 84% 6%, rgba(232,154,74,0.75) 0%, rgba(232,154,74,0.15) 14%, transparent 26%),
      radial-gradient(ellipse at 78% 55%, rgba(217,221,226,0.85) 0%, rgba(190,198,208,0.55) 26%, transparent 48%),
      linear-gradient(120deg, var(--navy) 0%, var(--slate) 55%, #2a3340 100%);
  }
  .banner__shade {
    position: absolute;
    inset: 0;
    background: linear-gradient(90deg,
      rgba(22,38,58,0.97) 0%,
      rgba(22,38,58,0.93) 34%,
      rgba(22,38,58,0.72) 50%,
      rgba(22,38,58,0.25) 66%,
      rgba(22,38,58,0) 80%);
  }
  .brand {
    position: absolute;
    left: 66px;
    top: 36px;
    display: flex;
    align-items: center;
    gap: 12px;
  }
  .brand__mark {
    width: 26px;
    height: 26px;
    background: var(--white);
  }
  .brand__name {
    font-weight: 700;
    font-size: 22px;
    letter-spacing: 0.5px;
    line-height: 1;
    color: var(--white);
  }
  .welcome {
    position: absolute;
    left: 78px;
    top: 123px;
    margin: 0;
    font-weight: 700;
    font-size: 17px;
    letter-spacing: 0.3px;
    color: var(--teal);
  }
  .headline {
    position: absolute;
    left: 77px;
    top: 161px;
    margin: 0;
    font-weight: 700;
    font-size: 35px;
    line-height: 49px;
    letter-spacing: 0.3px;
    text-transform: uppercase;
  }
  .intro {
    position: absolute;
    left: 78px;
    top: 313px;
    margin: 0;
    font-weight: 700;
    font-size: 12px;
    line-height: 27px;
    letter-spacing: 0.2px;
    text-transform: uppercase;
    white-space: nowrap;
    color: var(--white);
  }
  .ref-code {
    position: absolute;
    right: 16px;
    bottom: 11px;
    font-size: 11px;
    font-weight: 600;
    color: var(--soft-white);
  }
</style>
</head>
<body>
  <div class="banner">
    <div class="banner__photo" role="img" aria-label="Photo of hands working at a laptop and calculator on a desk covered with tax forms, lit by warm light"></div>
    <div class="banner__shade"></div>

    <div class="brand">
      <span class="brand__mark"></span>
      <span class="brand__name">SERENOVA LAW FIRM, PLLC</span>
    </div>

    <p class="welcome">WELCOME TO SERENOVA</p>

    <h1 class="headline">Estate Planning<br>&amp; Financial Planning<br>Under One Roof</h1>

    <p class="intro">Estate planning and financial planning isn't<br>just for the ultra-wealthy. We're here to help<br>families plan for their legacy and protect<br>their wealth</p>

    <span class="ref-code">C48</span>
  </div>
</body>
</html>
```